Ward Compass Business Card Design*

We need a business card design for our company Ward Compass. Our company is specialized in providing online consulting services regarding medical institutions, hospitals and doctors. We work with patients worldwide looking to choose between healthcare providers. We have a website you may use as a reference, where we list doctors and clinics worldwide. So we target Medical providers as well as patients worldwide.
Target Market(s)
Medical Providers and patients around the world
Industry/Entity Type
Medical
Contact Information for Business Card
Salwa Kettani
CEO
+90 612 348 2175
info@wardcompass.example
www.wardcompass.example
14 Annakhil 7 H.R.B. Rabat, Morocco
Requirements
Must have
- Company logo/name on one full side, personal info and smaller logo and company name on the other side.
Nice to have
- Smart and elegant design

```html
<!DOCTYPE html>
<html lang="en">
<head>
<meta charset="utf-8">
<title>Ward Compass – Business Card</title>
<link href="https://fonts.googleapis.com/css2?family=Lato:wght@400;700&family=Montserrat:wght@500;600&display=swap" rel="stylesheet">
<style>
  :root {
    --backdrop: #3b3c3e;
    --blue-light: #34a8dc;
    --blue-deep: #2f74b8;
    --ink: #2b2b2b;
    --paper: #ffffff;
    --divider: #b8b8b8;
  }
  * { box-sizing: border-box; margin: 0; padding: 0; }
  html, body {
    width: 1200px; height: 1200px; overflow: hidden;
    background: var(--backdrop);
  }
  .canvas { position: relative; width: 1200px; height: 1200px; }

  .card {
    position: absolute; left: 170px; width: 860px; height: 490px;
    box-shadow: 0 12px 30px rgba(0,0,0,.35);
  }
  .card--front {
    top: 75px;
    border-radius: 120px 0 120px 0;
    background: linear-gradient(180deg, var(--blue-light) 0%, var(--blue-deep) 100%);
    display: flex; align-items: center; justify-content: center; gap: 22px;
  }
  .card--back {
    top: 635px;
    border-radius: 0 120px 0 120px;
    background: var(--paper);
  }

  .brand-dot { border-radius: 50%; flex: none; }
  .card--front .brand-dot { width: 62px; height: 62px; border: 9px solid var(--paper); }
  .brand-name {
    font-family: "Montserrat", sans-serif; font-weight: 600;
    letter-spacing: 1.5px; text-transform: uppercase;
  }
  .card--front .brand-name { color: var(--paper); font-size: 40px; }

  .back-brand {
    position: absolute; left: 0; top: 0; width: 410px; height: 490px;
    display: flex; flex-direction: column; align-items: center; justify-content: center; gap: 26px;
  }
  .back-brand .brand-dot { width: 150px; height: 150px; border: 26px solid var(--blue-deep); }
  .back-brand .brand-name { color: var(--blue-deep); font-size: 26px; }

  .divider {
    position: absolute; left: 410px; top: 90px; width: 1.5px; height: 310px;
    background: var(--divider);
  }

  .person {
    position: absolute; left: 460px; top: 128px;
    font-family: "Lato", sans-serif; color: var(--ink);
  }
  .person__name {
    font-size: 34px; letter-spacing: 1px; text-transform: uppercase; line-height: 1;
  }
  .person__first { font-weight: 700; color: var(--blue-deep); }
  .person__last { font-weight: 400; color: var(--blue-light); }
  .person__role { font-size: 22px; margin-top: 4px; letter-spacing: .5px; }

  .contacts { list-style: none; margin-top: 50px; font-size: 24px; line-height: 1.45; }
  .contacts li { display: flex; align-items: center; gap: 10px; }
  .contacts svg { width: 20px; height: 20px; fill: var(--blue-light); flex: none; }
</style>
</head>
<body>
<main class="canvas">
  <section class="card card--front" aria-label="Card front">
    <span class="brand-dot"></span>
    <span class="brand-name">Ward Compass</span>
  </section>

  <section class="card card--back" aria-label="Card back">
    <div class="back-brand">
      <span class="brand-dot"></span>
      <span class="brand-name">Ward Compass</span>
    </div>
    <div class="divider"></div>
    <div class="person">
      <h1 class="person__name"><span class="person__first">Salwa</span> <span class="person__last">Kettani</span></h1>
      <p class="person__role">CEO</p>
      <ul class="contacts">
        <li>
          <svg viewBox="0 0 24 24" aria-hidden="true"><path d="M6.6 10.8a15.1 15.1 0 0 0 6.6 6.6l2.2-2.2a1 1 0 0 1 1-.25 11.4 11.4 0 0 0 3.6.57 1 1 0 0 1 1 1V20a1 1 0 0 1-1 1A17 17 0 0 1 3 4a1 1 0 0 1 1-1h3.5a1 1 0 0 1 1 1c0 1.25.2 2.45.57 3.57a1 1 0 0 1-.25 1z"/></svg>
          +90 612 348 2175
        </li>
        <li>
          <svg viewBox="0 0 24 24" aria-hidden="true"><path d="M2 5h20v14H2zm2 2v.4l8 5 8-5V7zm0 2.8V17h16V9.8l-8 5z"/></svg>
          info@wardcompass.example
        </li>
        <li>
          <svg viewBox="0 0 24 24" aria-hidden="true"><circle cx="12" cy="12" r="10"/></svg>
          www.wardcompass.example
        </li>
      </ul>
    </div>
  </section>
</main>
</body>
</html>
```